Business card for Internet Marketing Consultant

Simple - need a nice business card design using the logo elements and colors. Keywords: Progressive, professional, stylish, minimalist. Please use the nb as part of the design.

Info for card:

Brendan Okafor
Internet Marketing Strategist
Phone: (520) 555-0148
Email: brendan@northbeamgrowth.com
Address: 2193 W. Larkmoor Ave., Ste. 118
Tucson, Arizona 85710

Website: www.northbeamgrowth.com

Industry/Entity Type

Business

Font styles to use
Sans Serif

```html
<!DOCTYPE html>
<html lang="en">
<head>
<meta charset="utf-8">
<title>Northbeam Growth — Business Card</title>
<link rel="stylesheet" href="https://fonts.googleapis.com/css2?family=Roboto:wght@400;500;700&display=swap">
<style>
  :root {
    --brand-blue: #2f6bb8;
    --brand-blue-light: #4a82c6;
    --brand-green: #5cb85f;
    --paper: #ffffff;
    --ink: #1f1f1f;
    --muted: #7a7a7a;
    --backdrop: #e9e7e3;
  }
  * { box-sizing: border-box; margin: 0; padding: 0; }
  html, body { width: 1200px; height: 900px; overflow: hidden; }
  body {
    background: var(--backdrop);
    font-family: "Roboto", Arial, sans-serif;
    display: flex;
    align-items: center;
    justify-content: center;
    gap: 60px;
  }
  .card {
    position: relative;
    width: 520px;
    height: 297px;
    overflow: hidden;
    background: var(--paper);
    box-shadow: 0 6px 18px rgba(0,0,0,0.15);
  }

  /* Front */
  .card-front .brand {
    position: absolute;
    left: 34px;
    top: 34px;
  }
  .brand-line {
    display: flex;
    align-items: center;
    gap: 10px;
  }
  .brand-square {
    width: 22px;
    height: 22px;
    background: var(--brand-green);
  }
  .brand-name {
    font-size: 38px;
    font-weight: 700;
    color: var(--brand-blue);
    letter-spacing: -0.5px;
    line-height: 1;
  }
  .brand-tagline {
    margin-top: 8px;
    margin-left: 32px;
    font-size: 11.5px;
    letter-spacing: 4.2px;
    color: var(--muted);
    text-transform: uppercase;
  }
  .contact-band {
    position: absolute;
    left: 0;
    right: 0;
    bottom: 0;
    height: 160px;
    background: linear-gradient(180deg, var(--brand-blue) 0%, var(--brand-blue-light) 100%);
    color: var(--paper);
    padding: 22px 34px 0;
  }
  .person-name {
    font-size: 21px;
    font-weight: 700;
  }
  .person-title {
    font-size: 12.5px;
    margin-top: 2px;
    margin-bottom: 14px;
  }
  .contact-list { list-style: none; }
  .contact-list li {
    display: flex;
    align-items: center;
    gap: 8px;
    font-size: 12.5px;
    margin-bottom: 6px;
  }
  .contact-icon { width: 15px; height: 15px; flex: none; }
  .accent-strip {
    position: absolute;
    left: 0;
    right: 0;
    bottom: 0;
    height: 10px;
    background: var(--brand-green);
  }

  /* Back */
  .card-back { background: var(--brand-blue); }
  .card-back .brand-center {
    position: absolute;
    left: 0;
    right: 0;
    top: 0;
    bottom: 46px;
    display: flex;
    align-items: center;
    justify-content: center;
  }
  .card-back .brand-name {
    color: var(--paper);
    font-size: 46px;
  }
  .address-strip {
    position: absolute;
    left: 0;
    right: 0;
    bottom: 0;
    height: 46px;
    background: var(--paper);
    color: var(--ink);
    font-size: 14px;
    display: flex;
    align-items: center;
    justify-content: center;
  }
</style>
</head>
<body>

  <section class="card card-front" aria-label="Business card front">
    <div class="brand">
      <div class="brand-line">
        <span class="brand-square"></span>
        <span class="brand-name">northbeamgrowth</span>
      </div>
      <p class="brand-tagline">Internet Marketing Strategies</p>
    </div>

    <div class="contact-band">
      <p class="person-name">Brendan Okafor</p>
      <p class="person-title">Internet Marketing Strategist</p>
      <ul class="contact-list">
        <li>
          <svg class="contact-icon" viewBox="0 0 16 16" aria-hidden="true">
            <rect width="16" height="16" rx="2" fill="#fff"/>
            <path d="M5 3.5l1.8 2.2-1 1.1a6.5 6.5 0 0 0 3.4 3.4l1.1-1 2.2 1.8-1.2 1.6C7.6 12.6 3.4 8.4 3.4 4.7z" fill="var(--brand-blue)"/>
          </svg>
          (520) 555-0148
        </li>
        <li>
          <svg class="contact-icon" viewBox="0 0 16 16" aria-hidden="true">
            <rect width="16" height="16" rx="2" fill="#fff"/>
            <rect x="3" y="4.5" width="10" height="7" fill="none" stroke="var(--brand-blue)" stroke-width="1.3"/>
            <path d="M3 4.5l5 4 5-4" fill="none" stroke="var(--brand-blue)" stroke-width="1.3"/>
          </svg>
          brendan@northbeamgrowth.com
        </li>
        <li>
          <svg class="contact-icon" viewBox="0 0 16 16" aria-hidden="true">
            <rect width="16" height="16" rx="2" fill="#fff"/>
            <circle cx="8" cy="8" r="4.8" fill="none" stroke="var(--brand-blue)" stroke-width="1.2"/>
            <path d="M3.2 8h9.6M8 3.2c-2 2.6-2 7 0 9.6M8 3.2c2 2.6 2 7 0 9.6" fill="none" stroke="var(--brand-blue)" stroke-width="1"/>
          </svg>
          www.northbeamgrowth.com
        </li>
      </ul>
    </div>
    <div class="accent-strip"></div>
  </section>

  <section class="card card-back" aria-label="Business card back">
    <div class="brand-center">
      <span class="brand-name">northbeamgrowth</span>
    </div>
    <p class="address-strip">2193 W. Larkmoor Ave., Ste. 118 Tucson, Arizona 85710</p>
  </section>

</body>
</html>
```